B2B flyer solution for charging infrastructures (One-Pager Din A4, double-sided)

We need a professional design for our flyer in format Din A4/both sides.
Attached you will find the content for the flyer, but we are looking for a modern, professional design.

Some background/context information:
- the product is about a solution for charging and billing of charging infrastructures (for electric cars) in companies
- target group: companies, esp. facility managers, fleet managers, controlling, CTO, CEO
- should be printed and available online
- our website (and most of our current design work): https://wendavo-netz.de

In the files you will find:
- photos of reference implementations of our solution (should be included in the flyer)
- stock photos (we are using the one you will find in the current flyer on our presentations, maybe you can use it too to keep some corporate identity.
- our logo
- the current flyer as PDF and as PowerPoint
- a sample presentation we also need for customer communication

It would be nice if the design will align with the existing design work, but bring fresh aspects and will be up-to-date and professional.

Target Market(s)

B2B, companies, fleet managers, facility managers, CTO, CIO

Industry/Entity Type

Enterprises, Charging Solutions for Electric Vehicles

Requirements
Nice to have
• Bright, light design, clean, readable

```html
<!DOCTYPE html>
<html lang="de">
<head>
<meta charset="utf-8">
<title>wendavo-netz Professional – Flyer Vorder- und Rückseite</title>
<link rel="stylesheet" href="https://fonts.googleapis.com/css2?family=Questrial&family=Poppins:wght@500;600&display=swap">
<style>
:root{
  --sky:#7dcdf5;
  --sky-light:#d9f1fd;
  --ink:#14141c;
  --navy:#1a3a8c;
  --purple:#9b3a9c;
  --magenta:#d0328a;
  --grey:#e2e3e6;
  --grey-dark:#c9cacd;
  --text:#2a2a2e;
  --white:#ffffff;
}
*{box-sizing:border-box;margin:0;padding:0}
html,body{width:1200px;height:900px;overflow:hidden;background:var(--white)}
body{position:relative;font-family:"Questrial",sans-serif;color:var(--text)}
.page{position:absolute;top:57px;width:515px;height:723px;overflow:hidden;background:var(--grey)}
.page--front{left:50px}
.page--back{left:639px}
.abs{position:absolute}
.brand{font-family:"Questrial",sans-serif;font-size:27px;color:var(--ink);letter-spacing:.2px;display:flex;align-items:center;gap:9px;white-space:nowrap}
.brand__dot{width:14px;height:14px;border-radius:50%;background:var(--magenta)}
.heading{font-family:"Poppins",sans-serif;font-weight:600;color:var(--ink);font-size:21px;line-height:1.1;white-space:nowrap}
.sub{font-size:12.5px;line-height:1.15;color:var(--ink)}
.small{font-size:8.6px;line-height:1.2;color:var(--ink)}
.band{background:var(--ink);color:var(--white);font-family:"Poppins",sans-serif;font-weight:600;white-space:nowrap}
.band--tagline{left:0;width:515px;height:31px;display:flex;align-items:center;justify-content:center;font-size:11.6px}
.plug{width:15px;height:17px;flex:none}
.item{display:flex;gap:8px;align-items:flex-start;color:var(--navy);font-size:10.4px;line-height:1.15}
.footer{left:0;right:0;bottom:0;height:49px;background:linear-gradient(180deg,var(--sky),var(--sky-light));display:flex;align-items:center;justify-content:center;gap:14px;font-family:"Poppins",sans-serif;font-weight:500;font-size:11.6px;color:var(--ink);white-space:nowrap}
.footer span{display:flex;align-items:center;gap:4px;white-space:nowrap}
.footer svg{width:14px;height:14px;flex:none}
.photo{position:absolute}
/* Vorderseite */
.hero{left:0;top:0;width:515px;height:247px;background:linear-gradient(120deg,var(--sky) 0%,var(--sky-light) 60%,#bfe6fa 100%)}
.hero__photo{left:300px;top:0;width:215px;height:247px;background:linear-gradient(100deg,rgba(40,45,55,0) 0%,#4a4f5a 35%,#2c2f36 100%)}
.benefits{left:0;top:283px;width:515px;height:114px;background:linear-gradient(180deg,var(--grey-dark),#eeeef0 50%,var(--grey))}
.services{left:222px;top:397px;width:293px;height:167px;background:linear-gradient(90deg,#9ad8f7,var(--sky))}
.services__photo{left:0;top:397px;width:222px;height:167px;background:linear-gradient(90deg,#e8e8e8 0%,#7d8088 35%,#4b4e55 100%)}
.bullet-dot{width:9px;height:9px;border-radius:50%;background:var(--magenta);flex:none;margin-top:1px}
.svc{display:flex;gap:7px;font-size:8.6px;line-height:1.2;color:var(--ink);margin-bottom:10px}
.contact{left:0;top:595px;width:515px;height:79px;text-align:center}
/* Rückseite */
.car-photo{left:0;top:0;width:515px;height:320px;background:linear-gradient(180deg,#8a8d92 0%,#6c6f75 45%,#f1f1f1 75%,#ececec 100%)}
.wave{left:0;top:0;width:515px;height:95px}
.audience{left:0;top:320px;width:515px;height:50px;background:var(--grey-dark);display:flex}
.audience__cell{flex:1;display:flex;flex-direction:column;align-items:center;justify-content:flex-end;padding-bottom:6px;font-size:8.6px;color:var(--ink);gap:5px;border-right:1px solid #a9aaad;white-space:nowrap}
.audience__cell:last-child{border-right:none}
.audience svg{height:22px}
.col-title{font-family:"Poppins",sans-serif;font-weight:600;font-size:10px;line-height:1.2;color:var(--ink)}
.col-intro{font-size:8.6px;line-height:1.2;color:var(--navy);margin:12px 0 8px}
.col .item{font-size:8.8px;margin-bottom:7px;gap:9px}
.col .plug{width:12px;height:13px}
</style>
</head>
<body>
<svg width="0" height="0" style="position:absolute" aria-hidden="true">
  <symbol id="plug" viewBox="0 0 20 22">
    <g fill="none" stroke="#9b3a9c" stroke-width="2.2" stroke-linecap="round" stroke-linejoin="round">
      <path d="M4 3 L9 8 M10 1 L14 5"/>
      <path d="M3 7 L12 16 Q9 19 6 16 L3 13 Q0 10 3 7Z"/>
      <path d="M6 4 L15 13"/>
      <path d="M12 16 L17 21"/>
    </g>
  </symbol>
</svg>

<!-- Vorderseite -->
<section class="page page--front">
  <div class="abs hero"></div>
  <div class="photo hero__photo" role="img" aria-label="Foto: Ladesäule mit eingestecktem blauen Ladestecker"></div>
  <div class="abs brand" style="left:29px;top:28px"><i class="brand__dot"></i>wendavo-netz.de</div>
  <h1 class="abs heading" style="left:29px;top:95px">wendavo-netz Professional</h1>
  <p class="abs sub" style="left:29px;top:118px">die maßgeschneiderte B2B-Abrechnungslösung<br>für Elektromobilität</p>
  <div class="abs" style="left:29px;top:157px;width:102px;height:2px;background:var(--ink)"></div>
  <p class="abs small" style="left:29px;top:175px">Lade-Infrastruktur-Abrechnungslösungen für<br>Unternehmen, damit Lade-Infrastruktur Erträge<br>statt Kosten produziert.</p>
  <p class="abs small" style="left:29px;top:216px">So wird Lade-Infrastruktur von einer<br>Kostenstelle zu einem Profitcenter</p>

  <svg class="abs" style="left:0;top:247px" width="515" height="37" viewBox="0 0 515 37" aria-hidden="true">
    <path d="M0 0 H515 V12 H450 C410 12 400 37 360 37 H0Z" fill="#14141c"/>
  </svg>
  <p class="abs band" style="left:25px;top:255px;background:none;font-size:14.5px">Mit wendavo-netz Professional profitieren:</p>

  <div class="abs benefits"></div>
  <div class="abs" style="left:34px;top:314px;width:210px">
    <div class="item" style="margin-bottom:10px"><svg class="plug"><use href="#plug"/></svg>Effizienter Verwaltung von<br>Lade-Infrastruktur</div>
    <div class="item"><svg class="plug"><use href="#plug"/></svg>Umfassende Full-Service-Betreuung</div>
  </div>
  <div class="abs" style="left:252px;top:314px;width:260px">
    <div class="item" style="margin-bottom:10px"><svg class="plug"><use href="#plug"/></svg>Nahtloser Integration in Ihre<br>kaufmännischen Prozesse</div>
    <div class="item"><svg class="plug"><use href="#plug"/></svg>Vielseitigen Abrechnungsmöglichkeiten</div>
  </div>

  <div class="photo services__photo" role="img" aria-label="Foto: Wallbox mit grünem Ladekabel in einem Parkhaus"></div>
  <div class="abs services"></div>
  <div class="abs" style="left:253px;top:408px;width:250px">
    <h2 class="heading" style="font-size:17px;margin-bottom:9px">Leistungen:</h2>
    <p class="svc"><i class="bullet-dot"></i>Vielseitige Abrechnungsmöglichkeiten für Fuhrpark, Mitarbeiter, Partnerunternehmen, Mieter, Kunden und andere.</p>
    <p class="svc"><i class="bullet-dot"></i>Full-Service-Betreuung (Monitoring, Abrechnung, Benutzerbetreuung)</p>
    <p class="svc"><i class="bullet-dot"></i>Integration in ihre Unternehmensabläufe</p>
    <p class="svc"><i class="bullet-dot"></i>Berücksichtigung von Eigentümer/Mieter-Konstellationen</p>
  </div>

  <div class="abs band band--tagline" style="top:564px">wendavo-netz - Die Abrechnungslösung für Lade-Infrastruktur in Unternehmen.</div>

  <div class="abs contact">
    <p style="margin-top:22px;font-size:10.4px;line-height:1.2;color:var(--navy)">Kontaktieren Sie uns Erfahren Sie mehr über wendavo-netz und wie wir Ihre<br>Abrechnungsanforderungen erfüllen können.</p>
    <p style="margin-top:4px;font-family:'Poppins',sans-serif;font-weight:600;font-size:13.4px;color:var(--navy)">Kontaktieren Sie uns für eine kostenlose Beratung:</p>
  </div>

  <div class="abs footer">
    <span><svg viewBox="0 0 16 12"><rect x=".5" y=".5" width="15" height="11" fill="#c04a9a"/><path d="M.5 .5 8 7 15.5 .5" fill="none" stroke="#fff"/></svg>info@wendavo-netz.de</span>
    <span><svg viewBox="0 0 16 16"><circle cx="8" cy="8" r="7" fill="none" stroke="#9b3a9c" stroke-width="1.5"/><path d="M1 8h14M8 1c-3 3-3 11 0 14M8 1c3 3 3 11 0 14" fill="none" stroke="#9b3a9c"/></svg>www.wendavo-netz.de</span>
    <span><svg viewBox="0 0 16 16"><path d="M3 1 6 4 4.5 6.5Q6 10 9.5 11.5L12 10 15 13 13 15Q6 15 1 3Z" fill="#c04a9a"/></svg>+49 (0) 3581 442 760</span>
  </div>
</section>

<!-- Rückseite -->
<section class="page page--back">
  <div class="photo car-photo" role="img" aria-label="Foto: dunkles Elektroauto in einer Tiefgarage an einer Wallbox"></div>
  <svg class="abs wave" viewBox="0 0 515 95" preserveAspectRatio="none" aria-hidden="true">
    <defs><linearGradient id="skyfade" x1="0" x2="1"><stop offset="0" stop-color="#7dcdf5"/><stop offset=".75" stop-color="#8fd3f5"/><stop offset="1" stop-color="#8fd3f5" stop-opacity="0"/></linearGradient></defs>
    <path d="M0 0H515V50C430 60 380 98 280 86C180 74 80 55 0 72Z" fill="url(#skyfade)"/>
  </svg>
  <div class="abs brand" style="left:27px;top:27px;color:var(--white)"><i class="brand__dot"></i>wendavo-netz.de</div>
  <h1 class="abs heading" style="left:27px;top:282px">wendavo-netz Professional</h1>
  <p class="abs sub" style="left:27px;top:304px">die Funktionen im Überblick</p>

  <div class="abs audience">
    <div class="audience__cell"><svg viewBox="0 0 50 16"><path d="M2 13V9l5-5h14l5 5v4ZM24 13V9l5-5h14l5 5v4Z" fill="#5e6066"/><circle cx="8" cy="14" r="2" fill="#333"/><circle cx="42" cy="14" r="2" fill="#333"/></svg>Fuhrpark, Dienstwagen</div>
    <div class="audience__cell"><svg viewBox="0 0 36 22"><g fill="#5e6066"><circle cx="8" cy="5" r="3.5"/><circle cx="28" cy="5" r="3.5"/><circle cx="18" cy="8" r="4"/><path d="M1 16q7-8 14 0ZM21 16q7-8 14 0ZM9 22q9-11 18 0Z"/></g></svg>Mitarbeiter Privatfahrzeuge</div>
    <div class="audience__cell"><svg viewBox="0 0 22 24"><g fill="#5e6066"><circle cx="5" cy="3" r="2.3"/><circle cx="11" cy="3" r="2.3"/><circle cx="17" cy="3" r="2.3"/><circle cx="5" cy="10" r="2.3"/><circle cx="11" cy="10" r="2.3"/><circle cx="17" cy="10" r="2.3"/><circle cx="8" cy="17" r="2.3"/><circle cx="14" cy="17" r="2.3"/><rect x="6" y="20" width="10" height="4"/></g></svg>Kunden und Gäste</div>
    <div class="audience__cell"><svg viewBox="0 0 26 22"><g fill="#5e6066"><rect x="1" y="9" width="7" height="13"/><rect x="9" y="1" width="8" height="21"/><rect x="18" y="5" width="7" height="17"/></g></svg>Vermieter, Eigentümer</div>
  </div>

  <div class="abs col" style="left:27px;top:384px;width:225px">
    <h2 class="col-title">Full-Service-Betreuung für sorgenfreies Management</h2>
    <p class="col-intro">wendavo-netz übernimmt auf Wunsch alle organisatorischen Belange bei der Verwaltung Ihrer Lade-Infrastruktur, einschließlich:</p>
    <div style="margin-left:-6px">
      <div class="item"><svg class="plug"><use href="#plug"/></svg>Monitoring</div>
      <div class="item"><svg class="plug"><use href="#plug"/></svg>Support</div>
      <div class="item"><svg class="plug"><use href="#plug"/></svg>User-Onboarding und -Support</div>
      <div class="item"><svg class="plug"><use href="#plug"/></svg>Handling von Zugangskarten</div>
      <div class="item"><svg class="plug"><use href="#plug"/></svg>Integration von firmeninternen Zugangstoken</div>
    </div>
  </div>
  <div class="abs col" style="left:273px;top:384px;width:232px">
    <h2 class="col-title">Perfekte Integration in kaufmännische Prozesse</h2>
    <p class="col-intro" style="margin-top:10px">wendavo-netz fügt sich nahtlos in die kaufmännischen Strukturen moderner Unternehmen ein und bietet:</p>
    <div style="margin-left:-18px">
      <div class="item"><svg class="plug"><use href="#plug"/></svg>Erweitertes Reporting</div>
      <div class="item"><svg class="plug"><use href="#plug"/></svg>Aufschlüsselung und Tarifierung nach Nutzergruppe</div>
      <div class="item"><svg class="plug"><use href="#plug"/></svg>Unterstützung unternehmensinterner Abrechnung und Verrechnung und/oder Zahlungseinzug durch wendavo-netz</div>
      <div class="item"><svg class="plug"><use href="#plug"/></svg>Schnittstellen zu Buchhaltung und Lohnbuchhaltung</div>
      <div class="item"><svg class="plug"><use href="#plug"/></svg>Bedarfsgerechte Anpassbarkeit</div>
    </div>
  </div>

  <div class="abs" style="left:27px;top:570px;width:462px;height:1px;background:var(--ink)"></div>
  <div class="abs" style="left:26px;top:580px;width:470px">
    <h3 class="col-title" style="font-size:10px">Besonderer Aspekt : Eigentümer-Mieter-Konstellationen</h3>
    <p class="small" style="font-size:8.5px">Häufige Situation: Der Mieter eines Objektes benötigt Lade-Infrastruktur, der Eigentümer/Verwalter möchte nicht zusätzlich belastet werden. Unterschiedliche Betreibermodelle für verschiedene Situationen (Langzeit-Mieter vs. Kurzzeit-Mieter) Kauf-, Miet- und Leasing-Optionen Kostenneutral für Eigentümer/Verwalter durch geeignete Abrechnungsmodelle</p>
  </div>

  <div class="abs band band--tagline" style="top:644px">wendavo-netz - Die Abrechnungslösung für Lade-Infrastruktur in Unternehmen.</div>

  <div class="abs footer">
    <span><svg viewBox="0 0 16 12"><rect x=".5" y=".5" width="15" height="11" fill="#c04a9a"/><path d="M.5 .5 8 7 15.5 .5" fill="none" stroke="#fff"/></svg>info@wendavo-netz.de</span>
    <span><svg viewBox="0 0 16 16"><circle cx="8" cy="8" r="7" fill="none" stroke="#9b3a9c" stroke-width="1.5"/><path d="M1 8h14M8 1c-3 3-3 11 0 14M8 1c3 3 3 11 0 14" fill="none" stroke="#9b3a9c"/></svg>www.wendavo-netz.de</span>
    <span><svg viewBox="0 0 16 16"><path d="M3 1 6 4 4.5 6.5Q6 10 9.5 11.5L12 10 15 13 13 15Q6 15 1 3Z" fill="#c04a9a"/></svg>+49 (0) 3581 442 760</span>
  </div>
</section>
</body>
</html>
```